Packaging for Hair Fibers Product

We are a start up company looking for a new packaging design for hair building fibers. These are aimed at predominantly men but also women as well. We already have a logo and i have the packaging design from our competitors. We are wanting to keep the look masculine as 90% of our users will be middle aged men. We would like the colours to be black and white but are open to other colours as well.
It will need to have our logo and the following somewhere on the front.
"Instant Fuller & Thicker Hair" & "Natural Hair Building Fibers" "28g" or "Net Weight 28g"
We only need the front of the packaging designed, please make the other sides of the packaging the same colour but blank.
Target Market(s)
Men 25+
Industry/Entity Type
Hair And Beauty
Requirements
Must have
- Logo which i have included. and the following somewhere on the front.
- "Instant Fuller & Thicker Hair" ; "Natural Hair Building Fibers" "28g" or "Net Weight 28g"
Nice to have
- Make it stand out from the competition or similar to the brisketto example.

```html
<!DOCTYPE html>
<html lang="en">
<head>
<meta charset="utf-8">
<title>Volumon Hair Fibers – Packaging Fronts</title>
<link rel="stylesheet" href="https://fonts.googleapis.com/css2?family=Open+Sans:wght@400;500&display=swap">
<style>
  :root {
    --box-black: #231f20;
    --box-side: #414042;
    --paper: #ffffff;
    --frame-line: #6d6e71;
    --ink-light: #ffffff;
    --ink-dark: #231f20;
  }
  * { margin: 0; padding: 0; box-sizing: border-box; }
  html, body {
    width: 1200px; height: 1200px; overflow: hidden;
    background: var(--paper);
    font-family: "Open Sans", Arial, sans-serif;
  }
  .canvas { position: relative; width: 1200px; height: 1200px; }

  .sheet {
    position: absolute;
    background: var(--paper);
    border: 1px solid var(--frame-line);
  }
  .sheet--back { left: 440px; top: -1px; width: 761px; height: 1127px; }
  .sheet--front { left: -1px; top: 126px; width: 643px; height: 876px; }

  .box-sides { position: absolute; left: 0; top: 0; width: 1200px; height: 1200px; }
  .box-side { fill: var(--box-side); }

  .pack-front {
    position: absolute;
    background: var(--box-black);
    color: var(--ink-light);
    text-align: center;
  }
  .pack-front--band { left: 109px; top: 246px; width: 345px; height: 639px; }
  .pack-front--mark { left: 742px; top: 158px; width: 378px; height: 744px; }

  .brand-band {
    position: absolute; left: 0; right: 0; top: 160px; height: 100px;
    background: var(--paper);
    display: flex; align-items: center; justify-content: center;
  }
  .brand-name {
    font-weight: 400;
    text-transform: uppercase;
    white-space: nowrap;
  }
  .pack-front--band .brand-name { color: var(--ink-dark); font-size: 40px; letter-spacing: 0.2em; padding-left: 0.2em; }
  .pack-front--mark .brand-name {
    position: absolute; left: 0; right: 0; top: 274px; line-height: 48px;
    color: var(--ink-light); font-size: 32px; letter-spacing: 0.3em; padding-left: 0.3em;
  }
  .brand-dot {
    position: absolute; left: 50%; top: 130px;
    width: 70px; height: 70px; margin-left: -35px;
    border: 2px solid var(--ink-light);
  }

  .tagline { position: absolute; left: 0; right: 0; font-weight: 400; white-space: nowrap; }
  .pack-front--band .tagline { top: 274px; line-height: 24px; font-size: 16px; }
  .pack-front--mark .tagline {
    top: 355px; height: 42px; line-height: 42px;
    background: var(--paper); color: var(--ink-dark); font-size: 23px;
  }

  .headline {
    position: absolute; text-align: left;
    font-weight: 500; letter-spacing: 0.04em; white-space: nowrap;
  }
  .pack-front--band .headline { left: 57px; top: 344px; font-size: 30px; line-height: 46px; }
  .pack-front--mark .headline { left: 62px; top: 426px; font-size: 36px; line-height: 52px; }

  .audience-badge {
    position: absolute; left: 50%;
    background: var(--paper); color: var(--ink-dark);
    border-radius: 50%;
    display: flex; align-items: center; justify-content: center;
    line-height: 1.2;
  }
  .pack-front--band .audience-badge { top: 476px; width: 77px; height: 77px; margin-left: -38px; font-size: 17px; }
  .pack-front--mark .audience-badge { top: 557px; width: 86px; height: 86px; margin-left: -43px; font-size: 20px; }

  .net-weight { position: absolute; left: 0; right: 0; }
  .pack-front--band .net-weight { top: 580px; line-height: 32px; font-size: 23px; }
  .pack-front--mark .net-weight { top: 674px; line-height: 36px; font-size: 26px; }
</style>
</head>
<body>
<main class="canvas">

  <div class="sheet sheet--back"></div>
  <div class="sheet sheet--front"></div>

  <svg class="box-sides" viewBox="0 0 1200 1200" aria-hidden="true">
    <polygon class="box-side" points="78,272 109,246 109,885 78,814"/>
    <polygon class="box-side" points="711,186 742,158 742,902 711,822"/>
  </svg>

  <section class="pack-front pack-front--band">
    <div class="brand-band"><span class="brand-name">Volumon</span></div>
    <p class="tagline">Natural Hair Building Fibers</p>
    <h2 class="headline">Instant Fuller<br>&amp; Thicker Hair</h2>
    <div class="audience-badge">FOR<br>MEN</div>
    <p class="net-weight">28g</p>
  </section>

  <section class="pack-front pack-front--mark">
    <span class="brand-dot"></span>
    <span class="brand-name">Volumon</span>
    <p class="tagline">Natural Hair Building Fibers</p>
    <h2 class="headline">Instant Fuller<br>&amp; Thicker Hair</h2>
    <div class="audience-badge">FOR<br>MEN</div>
    <p class="net-weight">28g</p>
  </section>

</main>
</body>
</html>
```